Chartered Professional Accounting Firm Needs a Business Card Design

We need a card design for an accounting firm based in Toronto, Ontario. The firm name is Pavel Ostrom Professional Corporation. The owner of the firm is a chartered professional accountant and a certified general accountant. Services of the firm include 60% tax preparation and consulting and 40% financial statements for corporation year-end. We would like a modern design. The color could be black, white, gray, blue or other color to bring more confidence to clients. The logo of the firm should be included in the design. Thanks

Name: Pavel Ostrom, CPA, CGA Address: 47 Maple Crest Rd. Richmond Hill, ON L7K 3B5 Telephone: (416) 562-3907 Fax:(416) 734-2165 Email: pavel@pavelostrom-example.ca

Accounting

```html
<!DOCTYPE html>
<html lang="en">
<head>
<meta charset="utf-8">
<title>Pavel Ostrom Professional Corporation — Business Card</title>
<link rel="stylesheet" href="https://fonts.googleapis.com/css2?family=Cinzel:wght@500;700&family=Questrial&display=swap">
<style>
  :root {
    --bg: #d9d9d6;
    --card: #ffffff;
    --card-shade: #f1f1f1;
    --blue: #35368a;
    --grey: #8c8c8c;
    --grey-dark: #5f5f5f;
    --text: #3c3c3c;
    --rule: #b9b9b9;
  }
  * { box-sizing: border-box; margin: 0; padding: 0; }
  html, body { width: 1200px; height: 871px; overflow: hidden; }
  body {
    background: var(--bg);
    position: relative;
    font-family: "Questrial", sans-serif;
  }
  .card {
    position: absolute;
    left: 270px;
    width: 660px;
    height: 377px;
    background: linear-gradient(135deg, var(--card) 0%, var(--card-shade) 100%);
    box-shadow: 0 6px 18px rgba(0,0,0,0.18);
    overflow: hidden;
  }
  .card--back { top: 38px; }
  .card--front { top: 456px; }

  .firm-lockup { position: absolute; display: flex; align-items: flex-start; gap: 12px; }
  .firm-lockup__mark { width: 40px; height: 40px; background: var(--blue); flex: none; margin-top: 2px; }
  .firm-lockup__name {
    font-family: "Cinzel", serif; font-weight: 700; color: var(--blue);
    font-size: 24px; line-height: 1; letter-spacing: 0.5px; text-transform: uppercase;
  }
  .firm-lockup__name small { display: block; font-size: 13px; margin-top: 3px; letter-spacing: 0.6px; }
  .firm-lockup__credentials {
    font-family: "Cinzel", serif; font-weight: 500; color: var(--grey);
    font-size: 10px; line-height: 1.25; letter-spacing: 1px; text-transform: uppercase; margin-top: 3px;
  }
  .card--back .firm-lockup { left: 330px; top: 235px; }

  .card--front .firm-lockup { left: 160px; top: 34px; }
  .card--front .firm-lockup__name { font-size: 21px; }

  .divider {
    position: absolute; left: 110px; right: 34px; top: 152px;
    height: 1px; background: var(--rule);
  }
  .address {
    position: absolute; left: 40px; top: 172px;
    font-size: 13px; line-height: 2; letter-spacing: 2px; color: var(--text);
  }
  .holder {
    position: absolute; right: 40px; top: 184px;
    font-family: "Cinzel", serif; font-weight: 700; color: var(--blue);
    font-size: 17px; letter-spacing: 3px;
  }
  .contact {
    position: absolute; right: 40px; top: 238px; list-style: none;
  }
  .contact li {
    display: flex; justify-content: flex-end; align-items: center; gap: 14px;
    font-size: 13px; letter-spacing: 2px; color: var(--text); line-height: 25px;
  }
  .contact svg { width: 16px; height: 14px; fill: none; stroke: var(--grey-dark); stroke-width: 1.4; }
  .band { position: absolute; bottom: 0; height: 14px; }
  .band--grey { left: 0; width: 300px; background: linear-gradient(#b3b3b3, #8e8e8e); }
  .band--blue { left: 300px; right: 0; background: var(--blue); }
</style>
</head>
<body>

<section class="card card--back" aria-label="Card back">
  <div class="firm-lockup">
    <span class="firm-lockup__mark"></span>
    <div>
      <p class="firm-lockup__name">Pavel Ostrom<small>Professional Corporation</small></p>
      <p class="firm-lockup__credentials">Chartered Professional Accountant<br>Certified General Accountant</p>
    </div>
  </div>
</section>

<section class="card card--front" aria-label="Card front">
  <div class="firm-lockup">
    <span class="firm-lockup__mark"></span>
    <div>
      <p class="firm-lockup__name">Pavel Ostrom<small>Professional Corporation</small></p>
      <p class="firm-lockup__credentials">Chartered Professional Accountant<br>Certified General Accountant</p>
    </div>
  </div>

  <div class="divider"></div>

  <address class="address" style="font-style:normal">
    47 Maple Crest<br>Rd. Richmond Hill<br>ON L7K 3B5
  </address>

  <p class="holder">Pavel Ostrom, CPA, CGA</p>

  <ul class="contact">
    <li>(416) 562-3907
      <svg viewBox="0 0 16 14" aria-label="Telephone"><path d="M2 5c0-2 3-3 6-3s6 1 6 3l-2 1-1-2H5L4 6z"/><rect x="3" y="7" width="10" height="6" rx="1"/></svg>
    </li>
    <li>(416) 734-2165
      <svg viewBox="0 0 16 14" aria-label="Fax"><rect x="4" y="1" width="8" height="4"/><rect x="1.5" y="5" width="13" height="6" rx="1"/><rect x="4" y="9" width="8" height="4"/></svg>
    </li>
    <li>pavel@pavelostrom-example.ca
      <svg viewBox="0 0 16 14" aria-label="Email"><rect x="1.5" y="2" width="13" height="10"/><path d="M1.5 2l6.5 6 6.5-6"/></svg>
    </li>
  </ul>

  <div class="band band--grey"></div>
  <div class="band band--blue"></div>
</section>

</body>
</html>
```